Coastal Learner Bureau business cards

Australian company about to start offering its services. We recruit international students to come to study English, vocational education and postgraduate courses in Australia. We help them find the institution and select the right city they want to come to Australia. We are a young, online oriented and supportive agency. Our clients are between 18 and 35 years old, mainly University students, young professionals or people with work experience. We provide much more information that any other agency offer. We administrate a Facebook group with more than 11.000 members that daily ask questions about general information when coming to Australia, while they are here and even after they leave the country

Target Market(s)

International students from South America, Central America and Europe

Industry/Entity Type

Student

Contact Information for Business Card

Tomas Bilbrea
Managing Director
tomas@kelvarin.com.au
www.kelvoria.com.au
+61 491058264
Melbourne, Australia

Font styles to use
Serif
Sans Serif

Colors

Designer to choose colors to be used in the design.

Requirements
Must have
• Horizontal design
• Standard business card size and shape. If font uses green or yellow colours, they will have to match the ones from the logo
Nice to have
• UPDATE: Use the contents of the green image to design one of the card sides. Use our logo in the background of that side as watermark.
• Passport image, or immigration stamps. A picture of the Yarra River (from Melbourne) would be cool as well.
Should not have
• Non-standard business card size and shape
• Not black as the background colour of any sides as we are not a VIP agency or a hight class service. We are orientes to young people and they like colours, pictures, something attractive.
• Vertical design
• NO YELLOW or BLACK AS THE BACKGROUND COLOUR OF ANY SIDE OF THE BIZ CARD

```html
<!DOCTYPE html>
<html lang="en">
<head>
<meta charset="utf-8">
<title>Coastal Learner Bureau – Business Cards</title>
<link href="https://fonts.googleapis.com/css2?family=Oswald:wght@600&family=Jost:wght@400;500&display=swap" rel="stylesheet">
<style>
  :root {
    --bg: #e4e4e4;
    --card: #ffffff;
    --green: #0f6b3f;
    --gold: #e7bb1f;
    --ink: #3c3c3c;
    --muted: #555555;
    --sky-top: #9cc4e6;
    --sky-mid: #d9d2b8;
    --river: #3e6f95;
    --trees: #4d7a3a;
  }
  * { box-sizing: border-box; margin: 0; padding: 0; }
  html, body { width: 1200px; height: 1000px; overflow: hidden; }
  body {
    background: var(--bg);
    font-family: "Jost", "Futura", sans-serif;
    position: relative;
  }
  .card {
    position: absolute;
    top: 345px;
    width: 540px;
    height: 309px;
    background: var(--card);
    box-shadow: 0 6px 16px rgba(0,0,0,0.22);
    overflow: hidden;
  }
  .card--front { left: 40px; }
  .card--back { left: 620px; }

  .card__wave { position: absolute; inset: 0; width: 100%; height: 100%; }

  .brand {
    position: absolute;
    top: 66px;
    right: 30px;
    display: flex;
    align-items: center;
    gap: 8px;
  }
  .brand__dot {
    width: 14px; height: 14px; border-radius: 50%;
    background: var(--gold);
  }
  .brand__name {
    font-family: "Jost", sans-serif;
    font-weight: 500;
    font-size: 30px;
    color: var(--green);
    letter-spacing: 0.5px;
  }

  .holder {
    position: absolute;
    left: 46px;
    top: 166px;
  }
  .holder__name {
    font-family: "Oswald", sans-serif;
    font-weight: 600;
    font-size: 25px;
    color: var(--green);
    letter-spacing: 0.8px;
    text-transform: uppercase;
    line-height: 1.1;
  }
  .holder__role {
    font-size: 14px;
    color: var(--ink);
    margin-top: 1px;
  }

  .contact {
    position: absolute;
    left: 46px;
    top: 228px;
    list-style: none;
  }
  .contact__item {
    display: flex;
    align-items: center;
    gap: 10px;
    font-size: 13.5px;
    color: var(--ink);
    letter-spacing: 0.4px;
    line-height: 19px;
  }
  .contact__icon { width: 10px; height: 10px; flex: none; }

  .location {
    position: absolute;
    right: 44px;
    top: 230px;
    text-align: right;
    font-size: 13.5px;
    line-height: 17px;
    color: var(--muted);
    letter-spacing: 0.4px;
  }

  .photo {
    position: absolute;
    inset: 18px 18px 18px 18px;
    background:
      linear-gradient(180deg, var(--sky-top) 0%, var(--sky-mid) 38%, var(--trees) 56%, var(--river) 70%, #2d5678 100%);
  }
</style>
</head>
<body>

  <section class="card card--front" aria-label="Business card front">
    <svg class="card__wave" viewBox="0 0 540 309" preserveAspectRatio="none" aria-hidden="true">
      <path d="M0 0 H452 C405 38 355 56 270 60 C170 64 60 64 0 106 Z" fill="var(--gold)"/>
      <path d="M0 0 H436 C392 32 345 48 265 51 C165 55 55 56 0 95 Z" fill="var(--green)"/>
    </svg>

    <div class="brand">
      <span class="brand__dot"></span>
      <span class="brand__name">Kelvoria</span>
    </div>

    <div class="holder">
      <h1 class="holder__name">Tomas Bilbrea</h1>
      <p class="holder__role">Managing Director</p>
    </div>

    <ul class="contact">
      <li class="contact__item">
        <svg class="contact__icon" viewBox="0 0 10 10" aria-hidden="true">
          <rect x="2.5" y="0.5" width="5" height="9" rx="1" fill="none" stroke="var(--green)" stroke-width="1"/>
          <circle cx="5" cy="8" r="0.6" fill="var(--green)"/>
        </svg>
        +61 491058264
      </li>
      <li class="contact__item">
        <svg class="contact__icon" viewBox="0 0 10 10" aria-hidden="true">
          <rect x="0.5" y="2" width="9" height="6.5" fill="var(--green)"/>
          <path d="M0.8 2.3 L5 5.6 L9.2 2.3" fill="none" stroke="#fff" stroke-width="0.9"/>
        </svg>
        tomas@kelvarin.com.au
      </li>
      <li class="contact__item">
        <svg class="contact__icon" viewBox="0 0 10 10" aria-hidden="true">
          <circle cx="4" cy="4" r="3" fill="none" stroke="var(--green)" stroke-width="1.4"/>
          <path d="M6.2 6.2 L9.2 9.2" stroke="var(--green)" stroke-width="1.6" stroke-linecap="round"/>
        </svg>
        www.kelvoria.com.au
      </li>
    </ul>

    <p class="location">Melbourne,<br>Australia</p>
  </section>

  <section class="card card--back" aria-label="Business card back">
    <div class="photo" role="img" aria-label="Photograph of the Yarra River in Melbourne with the city skyline under a bright sun"></div>
  </section>

</body>
</html>
```